Thistlewick Superfoods Packaging Design

We are looking for a design for our premium superfoods powders and blends. Packaging dimensions are 21cm x 13cm Kraft packaging (light brown background). This design should be a blueprint for other products that we will be marketing including lions mane mushroom, reishi mushroom, Chaga mushroom, Spirilina, bee pollen, açai powder and the like. The design should be clean but earthy, and the template replicable for other products.

```html
<!DOCTYPE html>
<html lang="en">
<head>
<meta charset="utf-8">
<title>Thistlewick Superfoods – Reishi Mushroom Label</title>
<link href="https://fonts.googleapis.com/css2?family=Quicksand:wght@500&family=Encode+Sans+Semi+Condensed:wght@300;400&family=Libre+Baskerville:ital,wght@1,700&display=swap" rel="stylesheet">
<style>
  :root {
    --kraft: #c3a47f;
    --mint: #c8ebe3;
    --ink: #141414;
    --ink-soft: #3a4a47;
    --peach: #f0b4a4;
    --strip: #f7f8f7;
    --badge-green: #5aa63c;
    --badge-light: #e6f1dd;
  }
  * { margin: 0; padding: 0; box-sizing: border-box; }
  html, body { width: 941px; height: 1200px; overflow: hidden; }
  body { background: var(--kraft); position: relative; }

  .label {
    position: absolute; left: 152px; top: 40px;
    width: 637px; height: 1120px;
    background: var(--mint);
    color: var(--ink);
  }

  .illustration { position: absolute; }
  .illustration--cap-side {
    left: 0; top: 0; width: 300px; height: 380px;
    border-radius: 0 48% 40% 0;
    background: radial-gradient(ellipse at 40% 40%, #5b6c69 0%, #2e3938 45%, rgba(46,57,56,0.15) 80%);
  }
  .illustration--cap-top {
    left: 298px; top: 0; width: 339px; height: 265px;
    border-radius: 0 0 48% 48%;
    background: radial-gradient(ellipse at 45% 35%, #3c4a48 0%, #2a3332 50%, rgba(42,51,50,0.2) 85%);
  }

  .brand {
    position: absolute; left: 334px; top: 300px; width: 218px;
    display: flex; align-items: center; justify-content: center; gap: 10px;
    font-family: "Encode Sans Semi Condensed", sans-serif;
    font-weight: 400; font-size: 16px; letter-spacing: 3px;
    line-height: 1.5; text-align: center; color: var(--ink);
  }
  .brand__dot { width: 12px; height: 12px; border-radius: 50%; background: var(--badge-green); flex: none; }

  .product-name {
    position: absolute; left: 70px; top: 388px;
    font-family: "Quicksand", sans-serif; font-weight: 500;
    font-size: 70px; line-height: 76px; letter-spacing: -2px;
    color: var(--ink);
  }
  .product-name span { display: block; }
  .product-name span + span { padding-left: 66px; }

  .intro {
    position: absolute; left: 70px; top: 544px; width: 250px;
    font-family: "Encode Sans Semi Condensed", sans-serif; font-weight: 300;
    font-size: 14.5px; line-height: 20.5px; text-transform: uppercase;
    color: var(--ink);
  }

  .facts { position: absolute; left: 73px; top: 708px; list-style: none; }
  .facts li { display: flex; align-items: center; height: 39px; }
  .facts__ratio {
    width: 36px;
    font-family: "Encode Sans Semi Condensed", sans-serif; font-weight: 300;
    font-size: 25px;
  }
  .facts__text {
    font-family: "Encode Sans Semi Condensed", sans-serif; font-weight: 400;
    font-size: 11.5px; line-height: 13px; text-transform: uppercase;
  }

  .description {
    position: absolute; left: 366px; top: 540px; width: 190px;
    font-family: "Libre Baskerville", serif; font-style: italic; font-weight: 700;
    font-size: 12.2px; line-height: 21.2px; color: var(--ink);
  }

  .info-strip {
    position: absolute; left: 0; bottom: 0; width: 100%; height: 230px;
    background: var(--strip);
    border-top: 3px solid var(--peach);
  }
  .badges { position: absolute; left: 72px; top: 40px; display: flex; gap: 10px; }
  .badge {
    width: 42px; height: 42px; border-radius: 50%;
    background: var(--badge-light); border: 4px solid var(--badge-green);
  }
  .badge--square { border-radius: 8px; }
  .net-weight {
    position: absolute; right: 88px; top: 48px;
    font-family: "Encode Sans Semi Condensed", sans-serif; font-weight: 400;
    font-size: 20px; color: var(--ink);
  }
</style>
</head>
<body>
  <main class="label">
    <div class="illustration illustration--cap-side" role="img" aria-label="Engraved ink illustration of a reishi mushroom seen from the side with its stem"></div>
    <div class="illustration illustration--cap-top" role="img" aria-label="Engraved ink illustration of a reishi mushroom cap seen from above"></div>

    <div class="brand">
      <span class="brand__dot"></span>
      <span>THISTLEWICK<br>SUPERFOODS</span>
    </div>

    <h1 class="product-name"><span>REISHI</span><span>MUSHROOM</span></h1>

    <p class="intro">Moringa, also known as ‘the miracle tree’, has been praised for it’s health benefits for thousands of years. It is extremely rich in healthy antioxidants and bioactive compounds. If fact it has:</p>

    <ul class="facts">
      <li><span class="facts__ratio">7x</span><span class="facts__text">The vitamin C<br>of oranges</span></li>
      <li><span class="facts__ratio">4x</span><span class="facts__text">The calcium<br>of milk</span></li>
      <li><span class="facts__ratio">3x</span><span class="facts__text">The potassium<br>of bananas</span></li>
      <li><span class="facts__ratio">3x</span><span class="facts__text">Iron<br>of spinich</span></li>
    </ul>

    <p class="description">The leaves contain all nine essential amino acids and traditionally used in assisting the healing of many ailments. The nutiritional diveristy is also known to reduce both cholesterol and blood sugar levels whilst and have serious anti-inflammatory benefits. Our 100% organic moringa is grown and harvested in it’s native enviornment, supporting premium superfood nutrition.</p>

    <footer class="info-strip">
      <div class="badges">
        <span class="badge"></span>
        <span class="badge"></span>
        <span class="badge badge--square"></span>
        <span class="badge"></span>
      </div>
      <span class="net-weight">250g</span>
    </footer>
  </main>
</body>
</html>
```